Resposive web site in 4 languages + image gallery + logo design

We need a web page, which will work on all devices.
I have uploaded web page concept.
Company name: Praxelun
Industry/Entity Type
It Company
Logo Text
quality matters
Coding
Coded - Design and coding required
Number of Pages Required
1 page

```html
<!DOCTYPE html>
<html lang="en">
<head>
<meta charset="utf-8">
<title>Praxelun</title>
<link href="https://fonts.googleapis.com/css2?family=Oswald:wght@300;400;500&family=Open+Sans:wght@400;600;700&display=swap" rel="stylesheet">
<style>
:root{
  --yellow:#fdb913;
  --yellow-dark:#f5a800;
  --ink:#333333;
  --muted:#6b6b6b;
  --page:#f4f5f7;
  --card:#ffffff;
  --line:#e3e3e3;
  --dark:#232323;
  --field:#3b3b3b;
  --white:#ffffff;
}
*{box-sizing:border-box;margin:0;padding:0}
html,body{width:1200px;height:2821px;overflow:hidden}
body{background:var(--page);font-family:"Open Sans",Arial,sans-serif;color:var(--ink);position:relative}
.abs{position:absolute}
/* hero */
.hero{position:absolute;left:0;top:0;width:1200px;height:596px}
.hero-photo{position:absolute;inset:0;background:radial-gradient(ellipse at 30% 70%,#6a4a2c 0%,#3b2a1c 40%,#17120d 100%)}
.hero-photo::after{content:"";position:absolute;inset:0;background:rgba(0,0,0,.35)}
.site-header{position:absolute;left:0;top:0;width:1200px;height:130px}
.brand{position:absolute;left:88px;top:46px;font-family:"Oswald",sans-serif;font-weight:500;font-size:36px;letter-spacing:3px;color:var(--white);line-height:40px}
.nav{position:absolute;top:57px;left:0;font-family:"Oswald",sans-serif;font-size:14px;color:var(--white)}
.nav a{position:absolute;white-space:nowrap;color:var(--white);text-decoration:none}
.nav a.active{color:var(--yellow)}
.lang{position:absolute;left:858px;top:47px;width:148px;height:38px;border:1px solid var(--white);color:var(--white);font-family:"Oswald",sans-serif;font-size:14px;padding:9px 12px}
.lang svg{position:absolute;right:12px;top:16px}
.social-box{position:absolute;top:47px;width:45px;height:38px;border:1px solid var(--white)}
.social-box span{position:absolute;left:18px;top:15px;width:8px;height:8px;background:var(--white);border-radius:50%}
.welcome{position:absolute;left:305px;top:195px;width:588px;text-align:center;color:var(--white);font-family:"Oswald",sans-serif;font-weight:300;font-size:44px;line-height:50px}
.hero-rule{position:absolute;left:305px;width:588px;height:1px;background:rgba(255,255,255,.75)}
.hero-name{position:absolute;left:305px;top:262px;width:588px;text-align:center;color:var(--white);font-family:"Oswald",sans-serif;font-weight:500;font-size:72px;letter-spacing:6px;line-height:80px}
.hero-text{position:absolute;left:290px;top:376px;width:620px;text-align:center;color:var(--white);font-size:12px;line-height:23px}
.hero-btn{position:absolute;left:493px;top:450px;width:214px;height:47px;background:var(--yellow);color:var(--white);font-family:"Oswald",sans-serif;font-size:14px;text-align:center;line-height:47px}
.arrow{position:absolute;top:275px;width:46px;height:46px;border:2px solid var(--white);border-radius:50%}
.arrow svg{position:absolute;left:14px;top:13px}
/* estimate band */
.estimate{position:absolute;left:0;top:596px;width:1200px;height:100px;background:var(--yellow)}
.estimate h2{position:absolute;left:124px;top:28px;font-family:"Oswald",sans-serif;font-weight:300;font-size:31px;color:var(--white);line-height:42px}
.quote-btn{position:absolute;left:878px;top:30px;width:181px;height:45px;border:2px solid var(--white);color:var(--white);font-family:"Oswald",sans-serif;font-size:17px;line-height:41px;text-align:center}
/* section heads */
.section-title{position:absolute;left:0;width:1200px;text-align:center;font-family:"Oswald",sans-serif;font-size:29px;line-height:40px;color:var(--ink)}
.section-title em{font-style:normal;color:var(--yellow)}
.divider{position:absolute;left:562px;width:76px;height:14px}
.lead{position:absolute;left:270px;width:660px;text-align:center;font-size:11.5px;line-height:24px;color:var(--muted)}
/* service cards */
.card{position:absolute;left:85px;width:1030px;height:318px;background:var(--card);border:1px solid var(--line);border-radius:3px}
.card-photo{position:absolute;top:18px;width:281px;height:239px}
.slider-dots{position:absolute;top:278px;display:flex;gap:4px}
.slider-dots i{width:7px;height:7px;border-radius:50%;background:#888}
.slider-dots i:first-child{background:var(--yellow)}
.card h3{position:absolute;top:27px;font-family:"Oswald",sans-serif;font-weight:400;font-size:22px;color:var(--yellow);line-height:30px}
.card p{position:absolute;top:70px;width:640px;font-size:11.5px;line-height:24px;color:var(--muted)}
.features{position:absolute;top:244px;height:74px;border-top:1px solid var(--line);display:flex}
.feature{flex:1;text-align:center;padding-top:8px;font-size:11px;color:var(--muted);font-family:"Open Sans",sans-serif;white-space:nowrap}
.feature svg{display:block;margin:0 auto 4px}
/* about */
.about-photo{position:absolute;left:85px;top:2052px;width:312px;height:230px;background:linear-gradient(135deg,#6e4a3d 0%,#4b3a35 55%,#2e2a28 100%)}
.about-photo span{position:absolute;left:126px;top:30px;font-family:"Oswald",sans-serif;font-weight:500;font-size:24px;letter-spacing:2px;color:var(--white)}
.about-text{position:absolute;left:436px;top:2056px;width:630px;font-size:11.5px;line-height:23px;color:var(--muted)}
.about-text p+p{margin-top:12px}
.read-more{position:absolute;left:436px;top:2254px;font-family:"Oswald",sans-serif;font-size:14px;color:var(--yellow)}
/* contact */
.contact{position:absolute;left:0;top:2338px;width:1200px;height:418px;background:linear-gradient(180deg,#262626,#1d1d1d)}
.contact .section-title{color:var(--white);top:26px}
.field{position:absolute;background:var(--field);color:#d9d9d9;font-size:12px;padding:10px 9px}
.send{position:absolute;left:96px;top:356px;width:105px;height:37px;background:var(--yellow);color:var(--white);font-family:"Oswald",sans-serif;font-size:15px;text-align:center;line-height:37px}
.contact-intro{position:absolute;left:630px;top:122px;width:470px;font-size:11.5px;line-height:22px;color:#6d6d6d}
.info h4{position:absolute;font-family:"Open Sans",sans-serif;font-weight:700;font-size:14px;color:var(--yellow)}
.info div{position:absolute;font-size:11px;color:#b5b5b5}
.dots-row{position:absolute;left:882px;top:322px;display:flex;gap:9px}
.dots-row i{width:11px;height:11px;border-radius:50%;background:#bdbdbd}
.footer{position:absolute;left:0;top:2756px;width:1200px;height:65px;background:linear-gradient(180deg,var(--yellow),var(--yellow-dark));text-align:center;color:var(--white);font-size:12px;line-height:65px}
</style>
</head>
<body>

<section class="hero">
  <div class="hero-photo" role="img" aria-label="Craftsman carving wood at a workbench with wood shavings"></div>
  <header class="site-header">
    <div class="brand">PRAXELUN</div>
    <nav class="nav">
      <a class="active" style="left:496px">HOME</a>
      <a style="left:579px">SERVICES</a>
      <a style="left:682px">ABOUT US</a>
      <a style="left:788px">CONTACT</a>
    </nav>
    <div class="lang">ENGLISH<svg width="10" height="6"><path d="M0 0h10L5 6z" fill="#fff"/></svg></div>
    <div class="social-box" style="left:1014px" aria-label="Social link"><span></span></div>
    <div class="social-box" style="left:1066px" aria-label="Social link"><span></span></div>
  </header>
  <div class="welcome">WELCOME TO</div>
  <div class="hero-rule" style="top:258px"></div>
  <div class="hero-name">PRAXELUN</div>
  <div class="hero-rule" style="top:345px"></div>
  <p class="hero-text">Sed ut perspiciatis unde omnis iste natus error sit voluptatem accusantium doloremque laudantium, totam rem ab illo inventore veritatis et quasi architecto beatae vitae dicta sunt explicabo.</p>
  <div class="hero-btn">CLICK HERE FOR MORE INFO</div>
  <div class="arrow" style="left:33px"><svg width="16" height="18"><path d="M11 2 4 9l7 7" stroke="#fff" stroke-width="2.5" fill="none"/></svg></div>
  <div class="arrow" style="left:1121px"><svg width="16" height="18"><path d="M5 2l7 7-7 7" stroke="#fff" stroke-width="2.5" fill="none"/></svg></div>
</section>

<section class="estimate">
  <h2>ARE YOU INTERESTED IN AN ESTIMATE?</h2>
  <div class="quote-btn">GET A QUOTE &nbsp;<svg width="14" height="14" style="vertical-align:-2px"><circle cx="7" cy="7" r="6" stroke="#fff" stroke-width="1.5" fill="none"/><path d="M5.5 4l3 3-3 3" stroke="#fff" stroke-width="1.5" fill="none"/></svg></div>
</section>

<h2 class="section-title" style="top:729px">OUR <em>SERVICES</em></h2>
<svg class="divider" style="top:779px" viewBox="0 0 76 14"><line x1="0" y1="7" x2="76" y2="7" stroke="#fdb913" stroke-width="1.5"/><circle cx="6" cy="7" r="4" fill="#fff" stroke="#fdb913" stroke-width="1.5"/><circle cx="38" cy="7" r="4" fill="#fff" stroke="#fdb913" stroke-width="1.5"/><circle cx="70" cy="7" r="4" fill="#fff" stroke="#fdb913" stroke-width="1.5"/></svg>
<p class="lead" style="top:803px">Sed ut perspiciatis unde omnis iste natus error sit voluptatem accusantium doloremque laudantium, totam rem illo inventore veritatis et quasi architecto beatae vitae dicta sunt explicabo.</p>

<!-- Woodworks -->
<article class="card" style="top:878px">
  <div class="card-photo" style="left:18px;background:linear-gradient(135deg,#7a5a3e,#b08a62 55%,#4a3626)" role="img" aria-label="Hands planing a wooden board"></div>
  <div class="slider-dots" style="left:134px"><i></i><i></i><i></i><i></i></div>
  <h3 style="left:331px">WOODWORKS</h3>
  <p style="left:331px">Timber is, in essence, a natural and warm material. Wood is also relatively durable and easy to work with, which has made it a favourite of builders throughout history. Our goal is to offer suitable products and quality furniture with installation and after sales service to all of our clients. In order to achieve this, we're ready to help our clients in all stages of construction from design to production and maintenance. Timber is, in essence, a natural and warm service to all of our clients. In order to achieve this, we're ready to help our clients in all stages of construction from design to production and maintenance.</p>
  <div class="features" style="left:318px;width:711px">
    <div class="feature"><svg width="28" height="24"><rect x="4" y="8" width="20" height="9" rx="2" fill="none" stroke="#888" stroke-width="1.5"/><path d="M2 10v8h24v-8M6 18v3M22 18v3" fill="none" stroke="#888" stroke-width="1.5"/></svg>FURNITURE</div>
    <div class="feature"><svg width="28" height="24"><path d="M6 22V8a8 6 0 0 1 16 0v14zM14 4v18M6 13h16" fill="none" stroke="#888" stroke-width="1.5"/></svg>WINDOWS</div>
    <div class="feature"><svg width="28" height="24"><path d="M9 22V3h10v19M6 22h16" fill="none" stroke="#888" stroke-width="1.5"/><circle cx="16" cy="13" r="1" fill="#888"/></svg>DOORS</div>
    <div class="feature"><svg width="28" height="24"><path d="M3 21h6v-5h6v-5h6V6h5" fill="none" stroke="#888" stroke-width="1.5"/><path d="M3 21 25 4" stroke="#888" stroke-width="1"/></svg>STAIRCASES</div>
    <div class="feature"><svg width="28" height="24"><path d="M5 5l18 16M23 5 5 21" stroke="#555" stroke-width="3"/></svg>WOODCARVING</div>
    <div class="feature"><svg width="28" height="24"><rect x="4" y="7" width="20" height="10" transform="rotate(-20 14 12)" fill="none" stroke="#888" stroke-width="1.5"/><path d="M7 14l14-5M7 11l14-5" stroke="#888"/></svg>GRAINING</div>
  </div>
</article>

<!-- Stoneworks -->
<article class="card" style="top:1223px">
  <h3 style="left:28px">STONEWORKS</h3>
  <p style="left:28px;width:660px">The natural stone found in the ground has been used in construction for centuries because of its durability. A structure GALLERY (sliders) built by a skilled craftsman from natural stone is unique, genuine when cut and durable, and perfect for our bracing climate. This category gallery: our experienced craftsmen are ready to help you in all stages of construction from planning to completion. The natural stone found in the ground has been used in construction for centuries because of its durability. A structure GALLERY (sliders) built by a skilled climate in all stages of construction from planning to completion.</p>
  <div class="features" style="left:18px;width:683px">
    <div class="feature"><svg width="28" height="24"><path d="M3 8h22M3 14h22M3 20h22M10 8v6M18 14v6M14 20" fill="none" stroke="#888" stroke-width="1.5"/></svg>WALLS</div>
    <div class="feature"><svg width="28" height="24"><path d="M4 20h20M7 20V11h14v9M5 11l9-6 9 6" fill="none" stroke="#888" stroke-width="1.5"/></svg>TERRACES</div>
    <div class="feature"><svg width="28" height="24"><path d="M10 3 6 22M18 3l4 19M13 7h2M12 13h4M11 19h6" fill="none" stroke="#888" stroke-width="1.5"/></svg>PATHS</div>
    <div class="feature"><svg width="28" height="24"><path d="M4 22V11h20v11M4 15h20M10 11V6h8v5" fill="none" stroke="#888" stroke-width="1.5"/></svg>OUTDOOR KITCHENS</div>
    <div class="feature"><svg width="28" height="24"><rect x="4" y="3" width="20" height="19" fill="none" stroke="#888" stroke-width="1.5"/><path d="M4 8h20M9 22v-8h10v8" fill="none" stroke="#888" stroke-width="1.5"/></svg>FIREPLACES</div>
    <div class="feature"><svg width="28" height="24"><path d="M8 22V10l6-6 6 6v12zM12 14h4v8" fill="none" stroke="#888" stroke-width="1.5"/></svg>SMOKERIES</div>
    <div class="feature"><svg width="28" height="24"><path d="M5 22V6l2-2 2 2v16M12 22V6l2-2 2 2v16M19 22V6l2-2 2 2v16M3 10h22M3 17h22" fill="none" stroke="#888" stroke-width="1.3"/></svg>FENCES</div>
  </div>
  <div class="card-photo" style="left:737px;width:280px;background:linear-gradient(135deg,#8d8d8d,#b9b7b2 50%,#5f5f5f)" role="img" aria-label="Paving stones being laid with a rubber mallet"></div>
  <div class="slider-dots" style="left:852px"><i></i><i></i><i></i><i></i></div>
</article>

<!-- Restoration -->
<article class="card" style="top:1567px">
  <div class="card-photo" style="left:18px;background:linear-gradient(135deg,#6b4a2a,#a87b3e 50%,#3b2a1f)" role="img" aria-label="Hands restoring a painted wooden surface"></div>
  <div class="slider-dots" style="left:134px"><i></i><i></i><i></i><i></i></div>
  <h3 style="left:331px">RESTORATION</h3>
  <p style="left:331px">Timber is, in essence, a natural and warm material. Wood is also relatively durable and easy to work with, which has made it a favourite of builders throughout history. Our goal is to offer suitable products and quality furniture with installation and after sales service to all of our clients. In order to achieve this, we're ready to help our clients in all stages of construction from design to production and maintenance. Timber is, in essence, a natural and warm service to all of our clients. In order to achieve this, we're ready to help our clients in all stages of construction from design to production and maintenance.</p>
  <div class="features" style="left:318px;width:711px">
    <div class="feature"><svg width="28" height="24"><rect x="4" y="8" width="20" height="9" rx="2" fill="none" stroke="#888" stroke-width="1.5"/><path d="M2 10v8h24v-8M6 18v3M22 18v3" fill="none" stroke="#888" stroke-width="1.5"/></svg>FURNITURE</div>
    <div class="feature"><svg width="28" height="24"><path d="M6 22V8a8 6 0 0 1 16 0v14zM14 4v18M6 13h16" fill="none" stroke="#888" stroke-width="1.5"/></svg>WINDOWS</div>
    <div class="feature"><svg width="28" height="24"><path d="M9 22V3h10v19M6 22h16" fill="none" stroke="#888" stroke-width="1.5"/><circle cx="16" cy="13" r="1" fill="#888"/></svg>DOORS</div>
    <div class="feature"><svg width="28" height="24"><path d="M3 21h6v-5h6v-5h6V6h5" fill="none" stroke="#888" stroke-width="1.5"/><path d="M3 21 25 4" stroke="#888" stroke-width="1"/></svg>STAIRCASES</div>
    <div class="feature"><svg width="28" height="24"><path d="M5 5l18 16M23 5 5 21" stroke="#555" stroke-width="3"/></svg>FLOORS</div>
    <div class="feature"><svg width="28" height="24"><rect x="4" y="7" width="20" height="10" transform="rotate(-20 14 12)" fill="none" stroke="#888" stroke-width="1.5"/><path d="M7 14l14-5M7 11l14-5" stroke="#888"/></svg>SPECIAL PROJECTS</div>
  </div>
</article>

<!-- About -->
<h2 class="section-title" style="top:1914px">ABOUT <em>US</em></h2>
<svg class="divider" style="top:1964px" viewBox="0 0 76 14"><line x1="0" y1="7" x2="76" y2="7" stroke="#fdb913" stroke-width="1.5"/><circle cx="6" cy="7" r="4" fill="#fff" stroke="#fdb913" stroke-width="1.5"/><circle cx="38" cy="7" r="4" fill="#fff" stroke="#fdb913" stroke-width="1.5"/><circle cx="70" cy="7" r="4" fill="#fff" stroke="#fdb913" stroke-width="1.5"/></svg>
<p class="lead" style="top:1985px">Sed ut perspiciatis unde omnis iste natus error sit voluptatem accusantium doloremque laudantium, totam rem illo inventore veritatis et quasi architecto beatae vitae dicta sunt explicabo.</p>
<div class="about-photo" role="img" aria-label="Interior with brick wall, sofa and wooden furniture"><span>PRAXELUN</span></div>
<div class="about-text">
  <p>Praxelun is a company whose business operations include making wooden products, restoration and building structures from natural stone. All of our products are made by craftsmen and specialists who have extensive experience and knowledge in their fields. Praxelun is a company whose business operations include making craftsmen and specialists who have extensive experience and knowledge in their fields.</p>
  <p>The products we offer are always handmade and we take the requests and ideas of the specific client into account. We always strive to achieve the best possible quality. The products we offer are always handmade and we and ideas of the specific client into account. We always strive to achieve the best possible quality.</p>
</div>
<div class="read-more">READ MORE INFO <svg width="14" height="14" style="vertical-align:-2px"><circle cx="7" cy="7" r="6" stroke="#fdb913" stroke-width="1.5" fill="none"/><path d="M5.5 4l3 3-3 3" stroke="#fdb913" stroke-width="1.5" fill="none"/></svg></div>

<!-- Contact -->
<section class="contact">
  <h2 class="section-title">CONTACT FORM</h2>
  <svg class="divider" style="top:76px" viewBox="0 0 76 14"><line x1="0" y1="7" x2="76" y2="7" stroke="#fdb913" stroke-width="1.5"/><circle cx="6" cy="7" r="4" fill="#232323" stroke="#fdb913" stroke-width="1.5"/><circle cx="38" cy="7" r="4" fill="#232323" stroke="#fdb913" stroke-width="1.5"/><circle cx="70" cy="7" r="4" fill="#232323" stroke="#fdb913" stroke-width="1.5"/></svg>
  <div class="field" style="left:96px;top:122px;width:243px;height:38px">Name:</div>
  <div class="field" style="left:348px;top:122px;width:243px;height:38px">Email:</div>
  <div class="field" style="left:96px;top:169px;width:243px;height:38px">Phone:</div>
  <div class="field" style="left:348px;top:169px;width:243px;height:38px">Subject:</div>
  <div class="field" style="left:96px;top:215px;width:495px;height:124px">Message:</div>
  <div class="send">SEND</div>
  <p class="contact-intro">Lorem ipsum dolor sit amet, consectetur adipiscing elit, sed do eiusmod tempor incididunt ut labore et dolore magna aliqua. Ut enim ad minim veniam, quis nostrud exercitation ullamco laboris nisi ut aliquip ex ea commodo consequat.</p>
  <div class="info">
    <h4 style="left:630px;top:202px">Address</h4>
    <div style="left:630px;top:236px">Vareli 12 10115 Norvik ESTLAND</div>
    <h4 style="left:882px;top:202px">Email Address</h4>
    <div style="left:882px;top:236px">General : &nbsp;hello@praxelun.ee</div>
    <h4 style="left:630px;top:292px">Phone</h4>
    <div style="left:630px;top:326px">Mobile : +372 55 01 2390</div>
    <h4 style="left:882px;top:292px">Social Media</h4>
  </div>
  <div class="dots-row" aria-label="Social media links"><i></i><i></i><i></i><i></i><i></i></div>
</section>

<footer class="footer">Copyright © 2016 Praxelun All Rights Reserved.</footer>

</body>
</html>
```